Security and Technology Website - Bold and Confident, Something Unexpected

Maple Wren Systems is launching its first website and we need a great design to bring our brand to life and generate DTC and B2B leads.

We have a good logo, but I am struggling with the creative vision to bring it all together. While our industry is Alarm Systems and Technology, we want to create a site that is more friendly and less 'typical' than your standard IT sites.

It Must:
1. Appeal to both men and women. The logo is a bit masculine, so the colors and icons must soften this.
2. Feel modern - we need to convey that we we use the latest technology.
3. Feel a bit high-end. We are not a budget solution.
4. Have a distinct iconography and photo treatment.
5. Feel layered - not just a series of stacked horizontal modules.

It Should Not:
1. Feel like your typical IT website.

Here are resources to get you started!
• Staging Site:
https://maple-wren-systems.shopfrontdemo.example/
Password: Piper

•Brand Guide: https://www.layoutboard.example/design/QKRmWpLcT4V/hNbq8Yf2-ZsKeRtDw7xp-QE/edit?utm_content=QKRmWpLcT4V&utm_campaign=designshare&utm_medium=link2&utm_source=sharebutton

• Logo and Fonts and Photos: :https://files.cloudlocker.example/folders/7HtPqWmZc3Kd9RbLx2VnYs8FgJe4UoAiT?usp=sharing

• Design Inspiration (don't feel limited by this): https://www.layoutboard.example/design/QKTnHsVbWe8/p7MfRz31xYqLcKdTu9GNBw/edit?utm_content=QKTnHsVbWe8&utm_campaign=designshare&utm_medium=link2&utm_source=sharebutton

______________

The winner will be asked to provide design files and finished PNGs of the overall design file, backgrounds, photo treatments/frames, and icons.

The winner will likely be engaged for a phase 2 to build out a product page.

Industry/Entity Type

Alarm Systems, Home Theatres, and Commercial IT Networking

Number of Pages Required

1 page

Font styles to use
Sans Serif

Colors
0054AA
0677BA
7BADD7
CADEEF
E8F1F8
0094D4
00A9DD
6FCCEA
C7EBF8
E9F6FB
EB3D1F
EC4F4E
F09395
F8D3D4
FCEDEE

Requirements
Must have
• 1. Appeal to both men and women. The logo is a bit masculine, so the colors and icons must soften this. 2. Feel modern - we need to convey that we we use the latest technology. 3. Feel a bit high-end. We are not a budget solution. 4. Have a distinct iconography and photo treatment. 5. Feel layered - not just a series of stacked horizontal modules.
Should not have
• 1. Should not feel like just another IT website.

```html
<!DOCTYPE html>
<html lang="en">
<head>
<meta charset="utf-8">
<title>Maple Wren Systems — Safer, Smarter, Faster</title>
<link href="https://fonts.googleapis.com/css2?family=Lexend+Deca:wght@500;700;800&family=Poppins:ital,wght@0,400;0,500;0,600;1,400&display=swap" rel="stylesheet">
<style>
:root{
  --blue:#0D4F96;
  --blue-deep:#0A4487;
  --blue-bright:#0054AA;
  --red:#E2151D;
  --ink:#1c1c1c;
  --muted:#8a8a8a;
  --line:#d4d4d4;
  --panel:#f3f3f3;
  --star:#F4A31B;
  --white:#ffffff;
}
*{box-sizing:border-box;margin:0;padding:0}
html,body{width:1200px;height:5190px;overflow:hidden}
body{font-family:"Poppins",sans-serif;color:var(--ink);background:var(--white);position:relative}
.abs{position:absolute}
.head{font-family:"Lexend Deca",sans-serif;font-weight:800;text-transform:uppercase;color:var(--blue);letter-spacing:.5px}
.red{color:var(--red)}
.center{text-align:center}

/* top bar */
.topbar{top:0;left:0;width:1200px;height:38px;background:var(--blue)}
.topbar nav{position:absolute;left:88px;top:0;height:38px;display:flex;gap:24px;align-items:center}
.topbar a,.topbar .quote{font-family:"Lexend Deca",sans-serif;font-weight:700;font-size:11px;color:#fff;text-decoration:none;text-transform:uppercase}
.topbar .quote{position:absolute;left:936px;top:0;width:173px;height:38px;background:var(--red);display:flex;align-items:center;justify-content:center}

/* header */
.header{top:38px;left:0;width:1200px;height:107px;background:#fff}
.brand{position:absolute;left:88px;top:22px;display:flex;align-items:center;gap:10px}
.brand .mark{width:22px;height:22px;background:var(--red)}
.brand .name{font-family:"Lexend Deca",sans-serif;font-weight:800;font-size:18px;line-height:20px;color:var(--blue);text-transform:uppercase}
.mainnav{position:absolute;left:395px;top:44px;display:flex;gap:18px}
.mainnav span{font-family:"Lexend Deca",sans-serif;font-weight:500;font-size:11.5px;color:var(--blue);text-transform:uppercase}
.mainnav span::after{content:" ⌄";font-size:11px}
.search{position:absolute;left:1096px;top:44px}

/* hero */
.hero{top:145px;left:0;width:1200px;height:620px;overflow:hidden}
.hero .photo{position:absolute;inset:0;background:linear-gradient(100deg,#f4f5f5 0%,#eceeed 35%,#dfe3e1 55%,#c9d1cc 75%,#b9c4bd 100%)}
.hero .shapes{position:absolute;inset:0}
.hero .kicker{position:absolute;left:88px;top:155px;font-family:"Lexend Deca",sans-serif;font-weight:500;font-size:15px;color:var(--blue);text-transform:uppercase}
.hero h1{position:absolute;left:88px;top:180px;font-size:62px;line-height:70px;font-family:"Lexend Deca",sans-serif;font-weight:800;color:var(--blue);letter-spacing:1px}
.hero .sub{position:absolute;left:88px;top:335px;font-family:"Lexend Deca",sans-serif;font-weight:700;font-size:21px;color:var(--blue);text-transform:uppercase}

/* section title */
.title{font-size:25px;width:1200px;left:0;text-align:center}

/* feature icons */
.feature{width:260px;text-align:center}
.feature svg{display:block;margin:0 auto}
.feature h3{font-family:"Lexend Deca",sans-serif;font-weight:700;font-size:17px;line-height:22px;color:var(--blue);text-transform:uppercase;margin-top:12px}
.feature p{font-size:11.5px;line-height:21px;color:var(--muted);margin-top:10px;padding:0 40px}
.arrows{display:flex;gap:6px}

/* monitoring band */
.band{top:1399px;left:0;width:1200px;height:258px;background:var(--red)}
.band h2{position:absolute;left:105px;top:48px;font-family:"Lexend Deca",sans-serif;font-weight:800;font-size:44px;color:#fff}
.band p{position:absolute;left:105px;top:108px;width:580px;font-size:12px;line-height:22px;color:#fff}
.btn{display:flex;align-items:center;justify-content:center;font-family:"Lexend Deca",sans-serif;font-weight:700;font-size:11px;text-transform:uppercase;text-decoration:none}
.btn-blue{background:var(--blue);color:#fff}
.btn-red{background:var(--red);color:#fff}
.btn-outline{border:2px solid var(--red);color:var(--red);background:#fff}
.band .btn{position:absolute;left:107px;top:173px;width:177px;height:38px}
.band .logo{position:absolute;left:826px;top:60px;width:268px;height:140px;display:flex;align-items:center;justify-content:center;gap:12px}
.band .logo .mark{width:28px;height:28px;background:#fff}
.band .logo .name{font-family:"Lexend Deca",sans-serif;font-weight:800;font-size:30px;line-height:34px;color:#fff;text-transform:uppercase}

/* founder */
.founder-photo{left:88px;top:1773px;width:439px;height:478px;background:radial-gradient(ellipse at 50% 35%,#6e6f71 0%,#4a4b4d 60%,#3a3b3d 100%)}
.founder{left:572px;top:1806px;width:540px}
.founder h2{font-size:25px;line-height:36px}
.founder p{font-size:11.5px;line-height:22px;color:var(--muted);margin-top:14px;width:530px}
.signature{width:130px;height:50px;margin-top:16px;background:linear-gradient(90deg,rgba(13,79,150,.18),rgba(13,79,150,.05))}
.founder .actions{display:flex;gap:10px;margin-top:24px}
.founder .actions .btn{height:38px}

/* products */
.products-band{top:2625px;left:0;width:1200px;height:199px;background:var(--blue)}
.card{top:2413px;width:317px;height:331px;background:#f4f4f4}
.card .img{height:212px}
.card h3{font-family:"Lexend Deca",sans-serif;font-weight:700;font-size:16px;color:var(--blue);text-transform:uppercase;margin:22px 0 0 18px}
.card p{font-size:12.5px;line-height:23px;color:#666;margin:4px 18px 0 18px}

/* steps */
.step{width:300px;text-align:center}
.step .num{position:absolute;left:-14px;top:40px;font-family:"Lexend Deca",sans-serif;font-weight:800;font-size:86px;color:#eeeeee;line-height:1}

/* testimonials */
.quote-card{top:3436px;width:329px;height:232px;background:#f4f4f4;padding:70px 28px 0 28px}
.quote-card .q{position:absolute;left:26px;top:18px}
.stars{position:absolute;left:28px;top:50px;color:var(--star);font-size:21px;letter-spacing:4px}
.quote-card p{font-size:11.5px;line-height:22px;font-style:italic;color:#555;margin-top:22px}
.quote-card .who{font-family:"Lexend Deca",sans-serif;font-size:10.5px;font-weight:500;color:var(--blue);text-transform:uppercase;margin-top:10px}

/* partners */
.partners{top:3835px;left:88px;width:1024px;display:flex;justify-content:space-between;align-items:center}
.partners span{font-family:"Lexend Deca",sans-serif;font-weight:700;font-size:40px;color:#dcdcdc;text-transform:uppercase}

/* form */
.form{left:250px;top:4119px;width:700px;height:445px;background:var(--panel)}
.field label{display:block;font-family:"Lexend Deca",sans-serif;font-size:10.5px;font-weight:500;color:var(--ink);text-transform:uppercase;margin-bottom:6px}
.field .input{height:45px;background:#fff;border:1.5px solid #b9b9b9;font-size:12px;color:#888;padding:13px 18px}
.field .area{height:105px}
.form .submit{position:absolute;left:267px;top:364px;width:163px;height:44px;font-size:14px}

/* footer */
.footer{top:4662px;left:0;width:1200px;height:528px;background:var(--blue-deep);color:#fff}
.footer h2{position:absolute;left:88px;top:60px;font-size:25px;color:#fff}
.footer .tag{position:absolute;left:90px;top:101px;font-size:11.5px}
.footer .email{position:absolute;left:688px;top:64px;width:298px;height:39px;background:#fff;color:var(--blue);font-family:"Lexend Deca",sans-serif;font-size:11px;padding:12px 16px;text-transform:uppercase}
.footer .signup{position:absolute;left:994px;top:64px;width:115px;height:39px}
.footer .rule{position:absolute;left:88px;top:153px;width:1024px;height:1px;background:rgba(255,255,255,.45)}
.footer .rule.b{top:463px}
.footer .flogo{position:absolute;left:125px;top:240px;width:182px;display:flex;align-items:center;gap:10px}
.footer .flogo .mark{width:26px;height:26px;background:#fff}
.footer .flogo .name{font-family:"Lexend Deca",sans-serif;font-weight:800;font-size:22px;line-height:26px;text-transform:uppercase}
.social{position:absolute;top:380px;width:44px;height:44px;border-radius:50%}
.col{position:absolute;top:206px}
.col h4{font-family:"Lexend Deca",sans-serif;font-weight:500;font-size:15px;text-transform:uppercase;margin-bottom:14px}
.col li{list-style:none;font-size:12px;line-height:27px}
.contact-row{display:flex;gap:8px;font-size:11.5px;line-height:17px;margin-bottom:16px}
.contact-row b{font-family:"Lexend Deca",sans-serif;font-size:11px;text-transform:uppercase;display:block}
.copy{position:absolute;left:0;top:488px;width:1200px;text-align:center;font-family:"Lexend Deca",sans-serif;font-size:10.5px;text-transform:uppercase}
.totop{position:absolute;left:1134px;top:478px;width:38px;height:38px;border-radius:50%;background:var(--red)}
</style>
</head>
<body>

<div class="abs topbar">
  <nav><a href="#">About</a><a href="#">Project Consulting</a><a href="#">Contact</a></nav>
  <a class="quote" href="#">Request a Quote</a>
</div>

<header class="abs header">
  <div class="brand"><span class="mark"></span><span class="name">Maple Wren<br>Systems</span></div>
  <div class="mainnav"><span>Electronic Security</span><span>Audio + Video</span><span>Networking + Communication</span><span>Cabling</span></div>
  <svg class="search" width="16" height="16" viewBox="0 0 16 16"><circle cx="6.5" cy="6.5" r="5" fill="none" stroke="#0D4F96" stroke-width="2"/><line x1="10.5" y1="10.5" x2="15" y2="15" stroke="#0D4F96" stroke-width="2"/></svg>
</header>

<section class="abs hero">
  <div class="photo" role="img" aria-label="Faded photo of a woman on a video call at her laptop in a bright office"></div>
  <svg class="shapes" width="1200" height="620" viewBox="0 0 1200 620">
    <polygon points="1000,230 1200,70 1200,620 1115,620" fill="#0D4F96"/>
    <polygon points="930,430 1000,230 1115,620 1020,620" fill="#ffffff" opacity=".35"/>
    <polygon points="1030,0 1200,0 1200,70 1120,140" fill="#E2151D"/>
    <polygon points="0,520 565,520 525,620 0,620" fill="#0D4F96"/>
    <polygon points="565,520 610,520 570,620 525,620" fill="#ffffff" opacity=".6"/>
    <polygon points="0,590 200,590 180,620 0,620" fill="#0A4487"/>
  </svg>
  <div class="kicker">Proudly serving Middle Tennessee</div>
  <h1>SAFER <span class="red">SMARTER</span><br>FASTER.</h1>
  <div class="sub">Homes + Businesses</div>
</section>

<h2 class="abs head title" style="top:863px">Connect + <span class="red">Protect</span> Your World</h2>

<div class="abs feature" style="left:55px;top:926px">
  <svg width="150" height="124" viewBox="0 0 150 124">
    <path d="M4 24V4h28M146 24V4h-28" fill="none" stroke="#E2151D" stroke-width="6"/>
    <path d="M45 104l30 14 30-14" fill="none" stroke="#E2151D" stroke-width="7"/>
    <rect x="55" y="26" width="32" height="52" fill="none" stroke="#0D4F96" stroke-width="3"/>
    <path d="M55 26l18 8v52l-18-8z" fill="none" stroke="#0D4F96" stroke-width="3"/>
    <path d="M93 46a8 8 0 0 1 0 12M99 41a15 15 0 0 1 0 22" fill="none" stroke="#0D4F96" stroke-width="2.5"/>
  </svg>
  <h3>Entry &amp;<br>Motion Sensors</h3>
  <p>Pair text with an icon to focus on your chosen product, collection or blog post.</p>
</div>
<div class="abs feature" style="left:327px;top:926px">
  <svg width="150" height="124" viewBox="0 0 150 124">
    <path d="M4 24V4h28M146 24V4h-28" fill="none" stroke="#E2151D" stroke-width="6"/>
    <path d="M45 104l30 14 30-14" fill="none" stroke="#E2151D" stroke-width="7"/>
    <rect x="52" y="22" width="46" height="58" rx="6" fill="none" stroke="#0D4F96" stroke-width="3"/>
    <circle cx="75" cy="44" r="10" fill="none" stroke="#0D4F96" stroke-width="3"/>
    <path d="M67 72q8-14 16 0z" fill="none" stroke="#0D4F96" stroke-width="2.5"/>
    <line x1="58" y1="30" x2="66" y2="30" stroke="#0D4F96" stroke-width="2.5"/>
  </svg>
  <h3>Video<br>Doorbells</h3>
  <p>Pair text with an icon to focus on your chosen product, collection or blog post.</p>
</div>
<div class="abs feature" style="left:605px;top:926px">
  <svg width="150" height="124" viewBox="0 0 150 124">
    <path d="M4 24V4h28M146 24V4h-28" fill="none" stroke="#E2151D" stroke-width="6"/>
    <path d="M45 104l30 14 30-14" fill="none" stroke="#E2151D" stroke-width="7"/>
    <rect x="62" y="30" width="40" height="20" rx="3" transform="rotate(-25 82 40)" fill="none" stroke="#0D4F96" stroke-width="3"/>
    <path d="M78 54l-6 12H56M56 60v14" fill="none" stroke="#0D4F96" stroke-width="3"/>
    <circle cx="95" cy="33" r="3" fill="#0D4F96"/>
  </svg>
  <h3>Security<br>Cameras</h3>
  <p>Pair text with an icon to focus on your chosen product, collection or blog post.</p>
</div>
<div class="abs feature" style="left:883px;top:926px">
  <svg width="150" height="124" viewBox="0 0 150 124">
    <path d="M4 24V4h28M146 24V4h-28" fill="none" stroke="#E2151D" stroke-width="6"/>
    <path d="M45 104l30 14 30-14" fill="none" stroke="#E2151D" stroke-width="7"/>
    <circle cx="75" cy="50" r="26" fill="none" stroke="#0D4F96" stroke-width="3"/>
    <path d="M75 64l-11-11a7 7 0 0 1 11-9 7 7 0 0 1 11 9z" fill="none" stroke="#0D4F96" stroke-width="3"/>
  </svg>
  <h3>Pet-<br>Friendly</h3>
  <p>Pair text with an icon to focus on your chosen product, collection or blog post.</p>
</div>

<div class="abs arrows" style="left:544px;top:1218px">
  <svg width="54" height="72" viewBox="0 0 54 72"><polygon points="0,36 22,0 54,0 54,72 22,72" fill="#E2151D"/><path d="M38 36H18M26 28l-8 8 8 8" fill="none" stroke="#fff" stroke-width="2.5"/></svg>
  <svg width="54" height="72" viewBox="0 0 54 72"><polygon points="54,36 32,0 0,0 0,72 32,72" fill="#0D4F96"/><path d="M16 36h20M28 28l8 8-8 8" fill="none" stroke="#fff" stroke-width="2.5"/></svg>
</div>

<section class="abs band">
  <h2>24/7 MONITORING</h2>
  <p>Our team is always on guard. With always-on protection, we'll notify you of any suspicious activity. In emergencies, we'll monitor your local police, fire, or EMS.</p>
  <a class="btn btn-blue" href="#">Request a Quote</a>
  <div class="logo"><span class="mark"></span><span class="name">Maple Wren<br>Systems</span></div>
</section>

<div class="abs founder-photo" role="img" aria-label="Portrait of the founder in a navy suit and bow tie"></div>
<div class="abs founder">
  <h2 class="head">I founded Maple Wren Systems to bring together technology &amp; honest, reliable service.</h2>
  <p>I'm proud to call Tennessee home and even prouder to help keep its homes and businesses secure.</p>
  <p>Whether it's protecting or elevating your space, my goal is to make technology work for you.</p>
  <p>Think of us as your friendly, neighborhood tech expert—here to safeguard what matters most.</p>
  <div class="signature" role="img" aria-label="Signature of founder Graham Tolliver"></div>
  <div class="actions">
    <a class="btn btn-red" style="width:229px" href="#">Tell us how we can help</a>
    <a class="btn btn-outline" style="width:123px" href="#">About us</a>
  </div>
</div>

<h2 class="abs head title" style="top:2351px">Featured <span class="red">Products</span></h2>
<div class="abs products-band"></div>
<div class="abs card" style="left:105px">
  <div class="img" role="img" aria-label="Woman using a wall-mounted security keypad at home" style="background:linear-gradient(120deg,#d8d2cc,#b9a89a 55%,#8d7a6c)"></div>
  <h3>Affordable Security</h3>
  <p>For Homes • For Businesses</p>
</div>
<div class="abs card" style="left:441px">
  <div class="img" role="img" aria-label="Home theatre room with a large screen and lounge seating" style="background:linear-gradient(120deg,#c9a26a,#6f5a44 50%,#3a3029)"></div>
  <h3>Enviable Entertainment</h3>
  <p>Home Theatres • Smart Homes<br>• Whole Home A/V</p>
</div>
<div class="abs card" style="left:777px">
  <div class="img" role="img" aria-label="Colleagues on a video conference in a meeting room" style="background:linear-gradient(120deg,#d7dde2,#9eaab5 55%,#4a5664)"></div>
  <h3>Connected Businesses</h3>
  <p>Conference Systems • Phones<br>• Networking • WiFi</p>
</div>

<h2 class="abs head title" style="top:2923px;line-height:36px">A safer home or <span class="red">business</span> is as<br>easy as 1-2-3</h2>

<div class="abs step" style="left:142px;top:3020px">
  <span class="num">1</span>
  <svg width="150" height="124" viewBox="0 0 150 124"><path d="M4 24V4h28M146 24V4h-28" fill="none" stroke="#E2151D" stroke-width="6"/><path d="M45 104l30 14 30-14" fill="none" stroke="#E2151D" stroke-width="7"/><path d="M56 20h28l12 12v50H56z" fill="none" stroke="#0D4F96" stroke-width="3"/><text x="68" y="50" font-family="Poppins,sans-serif" font-size="18" fill="#0D4F96">$</text><line x1="64" y1="62" x2="88" y2="62" stroke="#0D4F96" stroke-width="2.5"/><line x1="64" y1="70" x2="88" y2="70" stroke="#0D4F96" stroke-width="2.5"/></svg>
  <div class="feature" style="width:300px"><h3>Build an<br>Instant Quote</h3><p>Our live-estimate builder will guide you through a few questions to help...</p></div>
</div>
<div class="abs step" style="left:448px;top:3020px">
  <span class="num">2</span>
  <svg width="150" height="124" viewBox="0 0 150 124"><path d="M4 24V4h28M146 24V4h-28" fill="none" stroke="#E2151D" stroke-width="6"/><path d="M45 104l30 14 30-14" fill="none" stroke="#E2151D" stroke-width="7"/><rect x="52" y="24" width="48" height="50" rx="4" fill="none" stroke="#0D4F96" stroke-width="3"/><line x1="52" y1="36" x2="100" y2="36" stroke="#0D4F96" stroke-width="3"/><circle cx="96" cy="70" r="10" fill="#fff" stroke="#0D4F96" stroke-width="3"/><path d="M60 46h8M72 46h8M84 46h8M60 56h8M72 56h8" stroke="#0D4F96" stroke-width="3"/></svg>
  <div class="feature" style="width:300px"><h3>Schedule<br>Installation</h3><p>Our trained techs are efficient and friendly. Southern-born and raised...</p></div>
</div>
<div class="abs step" style="left:754px;top:3020px">
  <span class="num">3</span>
  <svg width="150" height="124" viewBox="0 0 150 124"><path d="M4 24V4h28M146 24V4h-28" fill="none" stroke="#E2151D" stroke-width="6"/><path d="M45 104l30 14 30-14" fill="none" stroke="#E2151D" stroke-width="7"/><circle cx="75" cy="50" r="25" fill="none" stroke="#0D4F96" stroke-width="3"/><path d="M94 26l4-6M96 34l6-2" stroke="#0D4F96" stroke-width="3"/><text x="62" y="57" font-family="Lexend Deca,sans-serif" font-weight="700" font-size="18" fill="#0D4F96">24</text></svg>
  <div class="feature" style="width:300px"><h3>Stay<br>Secure 24/7</h3><p>Monitor your home through the app, receive instant alerts, and rely on professional...</p></div>
</div>

<h2 class="abs head title" style="top:3376px">What our <span class="red">clients</span> says</h2>

<div class="abs quote-card" style="left:88px">
  <svg class="q" width="50" height="36" viewBox="0 0 50 36"><path d="M2 14q0-12 14-14v6q-6 2-6 8h6v22H2zM28 14q0-12 14-14v6q-6 2-6 8h6v22H28z" fill="#F09395"/></svg>
  <div class="stars">★★★★★</div>
  <p>I wanted to upgrade my basic home theater but I didn't know who to trust. MWS analyzed my existing configuration, media preferences...</p>
  <div class="who">– Nora Pelham, Hendrick, TN</div>
</div>
<div class="abs quote-card" style="left:435px">
  <svg class="q" width="50" height="36" viewBox="0 0 50 36"><path d="M2 14q0-12 14-14v6q-6 2-6 8h6v22H2zM28 14q0-12 14-14v6q-6 2-6 8h6v22H28z" fill="#F09395"/></svg>
  <div class="stars">★★★★★</div>
  <p>Fantastic service!! Used HomeSentry and BrightNest in the past, and their customer service does not compare to Maple Wren! Installation and set up went smoothly...</p>
  <div class="who">– Dana K. White House, TN</div>
</div>
<div class="abs quote-card" style="left:781px">
  <svg class="q" width="50" height="36" viewBox="0 0 50 36"><path d="M2 14q0-12 14-14v6q-6 2-6 8h6v22H2zM28 14q0-12 14-14v6q-6 2-6 8h6v22H28z" fill="#F09395"/></svg>
  <div class="stars">★★★★★</div>
  <p>I couldn't be more impressed with the service we received for our condo's security system upgrade. The team was professional, efficient...</p>
  <div class="who">– Dana K. White House, TN</div>
</div>

<h2 class="abs head title" style="top:3768px">Service <span>Partners</span></h2>
<div class="abs partners"><span>Lockwell</span><span>Voxera</span><span>Lumora</span><span>Clearsight</span></div>
<div class="abs arrows" style="left:544px;top:3905px">
  <svg width="54" height="75" viewBox="0 0 54 72"><polygon points="0,36 22,0 54,0 54,72 22,72" fill="#E2151D"/><path d="M38 36H18M26 28l-8 8 8 8" fill="none" stroke="#fff" stroke-width="2.5"/></svg>
  <svg width="54" height="75" viewBox="0 0 54 72"><polygon points="54,36 32,0 0,0 0,72 32,72" fill="#0D4F96"/><path d="M16 36h20M28 28l8 8-8 8" fill="none" stroke="#fff" stroke-width="2.5"/></svg>
</div>

<h2 class="abs head title" style="top:4060px;color:var(--ink)">Get in <span class="red">touch</span> with us</h2>
<form class="abs form">
  <div class="abs field" style="left:26px;top:40px;width:320px"><label>Name*</label><div class="input">Enter name</div></div>
  <div class="abs field" style="left:354px;top:40px;width:316px"><label>Email*</label><div class="input">Enter email</div></div>
  <div class="abs field" style="left:26px;top:126px;width:320px"><label>Phone*</label><div class="input">Enter phone</div></div>
  <div class="abs field" style="left:354px;top:126px;width:316px"><label>Address*</label><div class="input">Enter address</div></div>
  <div class="abs field" style="left:26px;top:212px;width:644px"><label>Message*</label><div class="input area">Type your message</div></div>
  <div class="btn btn-red submit">Submit</div>
</form>

<footer class="abs footer">
  <h2 class="head">Subscribe to our newsletter</h2>
  <div class="tag">Security Tips, Special Offers, and More!</div>
  <div class="email">Your email address</div>
  <div class="btn btn-red signup">Sign up</div>
  <div class="rule"></div>

  <div class="flogo"><span class="mark"></span><span class="name">Maple Wren<br>Systems</span></div>
  <span class="social" style="left:165px;background:var(--red)" aria-label="Social profile"></span>
  <span class="social" style="left:220px;background:#2f68a8" aria-label="Social profile"></span>

  <div class="col" style="left:393px">
    <h4>Get in touch with us</h4>
    <div class="contact-row"><svg width="12" height="12" viewBox="0 0 12 12"><path d="M2 1l3 2-1 2q1 2 3 3l2-1 2 3-2 1Q4 10 1 3z" fill="#fff"/></svg><div><b>Phone</b>615.555.0142</div></div>
    <div class="contact-row"><svg width="12" height="14" viewBox="0 0 12 14"><path d="M6 13S1 8 1 5a5 5 0 0 1 10 0c0 3-5 8-5 8z" fill="#fff"/><circle cx="6" cy="5" r="2" fill="#0A4487"/></svg><div><b>Address:</b>240 Harbor Ridge Ln. Suite 3-110<br>Hendrick, TN 37000</div></div>
  </div>
  <div class="col" style="left:711px">
    <h4>Residential</h4>
    <ul><li>Home Security</li><li>Smart Homes</li><li>Home Theatres + A/V</li><li>WiFi</li><li>Cabling</li></ul>
  </div>
  <div class="col" style="left:934px">
    <h4>Commercial</h4>
    <ul><li>Audio Video</li><li>Cabling</li><li>Communication</li><li>Electronic Security</li><li>Project Consulting</li></ul>
  </div>

  <div class="rule b"></div>
  <div class="copy">©2024 Maple Wren Systems. All rights reserved.</div>
  <div class="totop"><svg width="38" height="38" viewBox="0 0 38 38"><path d="M14 21l5-5 5 5" fill="none" stroke="#fff" stroke-width="2"/></svg></div>
</footer>

</body>
</html>
```